KRL Stationery Design Project

Dear Designers,
We need a new stationery design for company to match our new logo.
Designers should provide a design for the following:
1. Business Card: 3.5x2 Inches.
2. Letterhead: A4 size.
3. Envelops: 25x35.5 Cm.
You can keep the Arabic name at the bottom of the logo Or you can use the separate attached Arabic Name.
Please refer to the attached logo guide for design information.
Sample Business Card information:
Name: Tarek Sowan
Position: Operation Manager
Tel: +966 920007164 Ex. 500
Fax: +966 (3)8842617
Mob: +966 (5)00263817
email: tarek@krl-example.com.sa
URL: www.krl-example.com.sa
Address:
Nakheel Heights, Suite 718
Zayed bin Omar Str.
Khobar, 31847
Saudi Arabia
Updates
Dear All,
Please note, we had uploaded our logo along with Arabic writing in Adobe illustrator format (.ai).
Regards,
Karim
Dear All,
A sample data for the business card had been added as per your request.
Regards,
Karim

```html
<!DOCTYPE html>
<html lang="en">
<head>
<meta charset="utf-8">
<title>KRL Business Card</title>
<link href="https://fonts.googleapis.com/css2?family=Open+Sans:ital,wght@0,400;0,700;1,700&display=swap" rel="stylesheet">
<style>
  :root {
    --navy: #0f2d52;
    --grey-line: #a6a8ab;
    --text: #333a44;
    --card: #ffffff;
    --backdrop: #1e1e1f;
  }
  * { margin: 0; padding: 0; box-sizing: border-box; }
  html, body {
    width: 960px; height: 1200px; overflow: hidden;
    background: var(--backdrop);
    font-family: "Open Sans", Arial, sans-serif;
  }
  .card {
    position: absolute;
    width: 840px; height: 480px;
    background: var(--card);
    border-radius: 32px;
    overflow: hidden;
    box-shadow: 0 6px 14px rgba(0,0,0,.5);
  }
  .card--front { left: 40px; top: 70px; }
  .card--back  { left: 57px; top: 624px; }

  .brand {
    position: absolute; left: 0; right: 0;
    display: flex; align-items: center; justify-content: center; gap: 22px;
    color: var(--navy);
  }
  .card--front .brand { top: 70px; height: 140px; }
  .card--back .brand  { top: 150px; height: 180px; }
  .brand__mark {
    border-radius: 50%; background: var(--navy);
  }
  .card--front .brand__mark { width: 54px; height: 54px; }
  .card--back .brand__mark  { width: 70px; height: 70px; }
  .brand__name { font-weight: 700; letter-spacing: 2px; line-height: 1; }
  .card--front .brand__name { font-size: 92px; }
  .card--back .brand__name  { font-size: 120px; }

  .person {
    position: absolute; left: 0; right: 0; top: 280px;
    text-align: center; color: var(--navy);
  }
  .person__name { font-size: 24px; }
  .person__role { font-size: 19px; }

  .contact {
    position: absolute; left: 0; right: 0; top: 328px;
    text-align: center; color: var(--text); font-size: 18px; line-height: 31px;
  }
  .contact b { font-style: italic; font-weight: 700; }
  .contact .sep { margin: 0 8px; }

  .footer-band {
    position: absolute; left: 0; bottom: 0; width: 840px; height: 80px;
  }
  .address {
    position: absolute; left: 0; right: 0; bottom: 14px;
    text-align: center; color: #fff; font-size: 18px;
  }
</style>
</head>
<body>
  <section class="card card--front">
    <div class="brand">
      <span class="brand__mark"></span>
      <span class="brand__name">KRL</span>
    </div>
    <div class="person">
      <span class="person__name">Your Name,</span>
      <span class="person__role">Designation</span>
    </div>
    <div class="contact">
      <div><b>t</b> : 123-123-1234<span class="sep">|</span><b>f</b> : 123-123-1234</div>
      <div><b>e</b> : info@krl-example.com.sa<span class="sep">|</span><b>w</b> : www.krl-example.com.sa</div>
    </div>
    <svg class="footer-band" viewBox="0 0 840 80" aria-hidden="true">
      <path d="M0 45 Q420 -10 840 45 L840 52 Q420 -2 0 52 Z" fill="var(--grey-line)"/>
      <path d="M0 55 Q420 8 840 55 L840 80 L0 80 Z" fill="var(--navy)"/>
    </svg>
    <div class="address">1234, Suite# 123, Street Name, State Name, Country Code</div>
  </section>

  <section class="card card--back">
    <div class="brand">
      <span class="brand__mark"></span>
      <span class="brand__name">KRL</span>
    </div>
  </section>
</body>
</html>
```